Coastline Premier Retreats Business Card Design

Design a business card for Coastline Premier Retreats. Look at the website for colors and reference. Card should have logo, name, title, office number, mobile number, email, URL and a tagline like, "Luxury Hotel & Resort Email Marketing" (This might change).

https://www.coastlinepremierretreats.example

The rest I will leave up to your imagination.

Contact Information for Business Card

Logo, name, title, office number, mobile number, email, URL and a tagline like, "Luxury Hotel & Resort Email Marketing" (This might change).

```html
<!DOCTYPE html>
<html lang="en">
<head>
<meta charset="utf-8">
<title>Coastline Premier Retreats – Business Card</title>
<link href="https://fonts.googleapis.com/css2?family=Montserrat:ital,wght@0,400;0,600;0,700;0,800;1,500&display=swap" rel="stylesheet">
<style>
  :root {
    --backdrop: #2a2a2a;
    --card: #1b1b1b;
    --orange: #f26d12;
    --white: #f4f4f4;
    --muted: #c9c9c9;
    --emboss: #2b2b2b;
  }
  * { box-sizing: border-box; margin: 0; padding: 0; }
  html, body { width: 1200px; height: 900px; overflow: hidden; }
  body {
    background: var(--backdrop);
    font-family: "Montserrat", Arial, sans-serif;
    position: relative;
  }
  .card {
    position: absolute;
    left: 250px;
    width: 700px;
    height: 400px;
    background: var(--card);
    box-shadow: 0 10px 30px rgba(0,0,0,.45);
    overflow: hidden;
  }
  .card--front { top: 33px; }
  .card--back { top: 467px; }

  /* Front */
  .identity {
    position: absolute;
    left: 52px;
    top: 62px;
    padding-left: 38px;
  }
  .identity__bar {
    position: absolute;
    left: 0; top: 2px;
    width: 24px; height: 30px;
    background: var(--orange);
  }
  .identity__name {
    font-weight: 800;
    font-size: 30px;
    letter-spacing: 1px;
    color: var(--orange);
    line-height: 1;
  }
  .identity__title {
    font-size: 14px;
    color: var(--white);
    margin-top: 4px;
  }
  .brand {
    position: absolute;
    right: 46px;
    top: 168px;
    display: flex;
    align-items: center;
    gap: 10px;
  }
  .brand__mark {
    width: 14px; height: 14px;
    background: var(--orange);
  }
  .brand__name {
    font-weight: 700;
    font-size: 21px;
    color: var(--white);
    letter-spacing: .5px;
  }
  .contact {
    position: absolute;
    right: 46px;
    top: 222px;
    width: 380px;
    color: var(--white);
    font-size: 14px;
    line-height: 1.45;
  }
  .contact__address { margin-bottom: 10px; }
  .contact__list { list-style: none; }
  .contact__item { display: flex; align-items: center; gap: 9px; }
  .contact__icon { width: 13px; height: 13px; flex: none; }
  .contact__accent { color: var(--orange); }

  /* Back */
  .watermark {
    position: absolute;
    left: 0; right: 0;
    top: 120px;
    text-align: center;
    font-weight: 800;
    font-size: 44px;
    letter-spacing: 1px;
    color: var(--emboss);
  }
  .tagline {
    position: absolute;
    left: 0; right: 0;
    top: 268px;
    text-align: center;
    font-style: italic;
    font-weight: 500;
    font-size: 22px;
    color: var(--orange);
  }
</style>
</head>
<body>

<section class="card card--front" aria-label="Business card front">
  <div class="identity">
    <span class="identity__bar"></span>
    <h1 class="identity__name">DANIEL MARSH</h1>
    <p class="identity__title">CEO/Founder</p>
  </div>

  <div class="brand">
    <span class="brand__mark"></span>
    <span class="brand__name">Coastline Premier Retreats</span>
  </div>

  <div class="contact">
    <p class="contact__address">Po Box, 480 Harbor Way<br>Seaside Bay, CA 90210</p>
    <ul class="contact__list">
      <li class="contact__item">
        <svg class="contact__icon" viewBox="0 0 12 12"><rect x="3" y="0.5" width="6" height="11" rx="1" fill="none" stroke="#f26d12" stroke-width="1.2"/><circle cx="6" cy="9.5" r=".7" fill="#f26d12"/></svg>
        <span>555.014.2200</span>
      </li>
      <li class="contact__item">
        <svg class="contact__icon" viewBox="0 0 12 12"><path d="M1 4c0-2 2-3 5-3s5 1 5 3l-2 1-1-1.5H4L3 5z" fill="#f26d12"/><rect x="2.5" y="6" width="7" height="5" rx="1" fill="#f26d12"/></svg>
        <span>+34 600 000 142</span>
      </li>
      <li class="contact__item">
        <svg class="contact__icon" viewBox="0 0 12 12"><rect x="0.5" y="2" width="11" height="8" fill="#f26d12"/><path d="M0.5 2 6 6.5 11.5 2" fill="none" stroke="#1b1b1b" stroke-width="1"/></svg>
        <span>info@coastlinepremierretreats.example</span>
      </li>
      <li class="contact__item">
        <svg class="contact__icon" viewBox="0 0 12 12"><circle cx="6" cy="6" r="5.4" fill="#f26d12"/><path d="M.8 6h10.4M6 .6c-2.5 3-2.5 7.8 0 10.8M6 .6c2.5 3 2.5 7.8 0 10.8" fill="none" stroke="#1b1b1b" stroke-width=".8"/></svg>
        <span>www.<span class="contact__accent">coastlinepremierretreats</span>.example</span>
      </li>
    </ul>
  </div>
</section>

<section class="card card--back" aria-label="Business card back">
  <p class="watermark">Coastline Premier Retreats</p>
  <p class="tagline">Luxury Hotel &amp; Resort Email Marketing</p>
</section>

</body>
</html>
```